real esate business card with company logo and name

we need a business card design for a real esate company

The company name is Walsh & Brand Pty Ltd, and we have our logo designed and will upload. We want classic or moden feel. Black or white background. looks more textured. Should include folowinginformations
Owen Walsh and Lucy Brand
Sales Agents & Onsite Manager
p: 07 5948 2063
F: 07 5948 2174
M:0431 857 219
3/42 Marlow Crescent, FERNLEA QLD 4213

We want this business card looks professonal. Thank you in advance.

Industry/Entity Type

Real Estate Agent

Contact Information for Business Card

Owen Walsh and Lucy Brand
Onsite Manager & Sales Agents
p: 07 5948 2063
M:0431 857 219

Font styles to use
Serif

Colors
000000
fbfbfb
333333
959595

Requirements
Must have
• company logo and name, black or white back ground

```html
<!DOCTYPE html>
<html lang="en">
<head>
<meta charset="utf-8">
<title>Walsh &amp; Brand Pty Ltd – Business Card</title>
<link rel="stylesheet" href="https://fonts.googleapis.com/css2?family=Cinzel:wght@400;600&family=Josefin+Sans:wght@400&display=swap">
<style>
  :root {
    --black: #000000;
    --white: #fbfbfb;
    --charcoal: #333333;
    --grey: #959595;
    --stage: #e4e4e4;
  }
  * { box-sizing: border-box; margin: 0; padding: 0; }
  html, body { width: 1200px; height: 913px; overflow: hidden; }
  body {
    background: var(--stage);
    display: flex;
    align-items: center;
    justify-content: center;
    gap: 60px;
  }
  .card {
    position: relative;
    width: 540px;
    height: 324px;
    border-radius: 14px;
    overflow: hidden;
    box-shadow: 0 8px 24px rgba(0,0,0,.18);
  }
  .card__edge { position: absolute; inset: 0; width: 100%; height: 100%; }

  /* Front */
  .card--front { background: var(--white); color: var(--black); }
  .contact-block { position: absolute; left: 64px; top: 52px; }
  .names {
    font-family: "Cinzel", serif;
    font-size: 21px;
    font-weight: 400;
    color: var(--black);
    letter-spacing: .5px;
  }
  .role {
    font-family: "Cinzel", serif;
    font-size: 12px;
    color: var(--grey);
    letter-spacing: .6px;
    margin-top: 4px;
  }
  .address {
    font-family: "Cinzel", serif;
    font-size: 13px;
    font-style: normal;
    color: var(--black);
    line-height: 1.35;
    margin-top: 14px;
  }
  .phones {
    position: absolute;
    left: 96px;
    bottom: 40px;
    list-style: none;
    font-family: "Cinzel", serif;
    font-size: 13px;
    color: var(--charcoal);
    line-height: 1.55;
  }
  .phones li { display: flex; align-items: center; gap: 8px; }
  .phones svg { width: 11px; height: 11px; fill: var(--charcoal); }

  .brand {
    position: absolute;
    display: flex;
    align-items: center;
    gap: 12px;
    font-family: "Josefin Sans", sans-serif;
    font-size: 17px;
    letter-spacing: 2px;
    white-space: nowrap;
  }
  .brand__mark { width: 16px; height: 16px; background: currentColor; }
  .card--front .brand { right: 34px; top: 196px; color: var(--grey); }

  /* Back */
  .card--back { background: var(--black); }
  .card--back .brand {
    left: 50%; top: 50%;
    transform: translate(-50%, -50%);
    color: var(--grey);
    font-size: 20px;
  }
</style>
</head>
<body>

  <section class="card card--front" aria-label="Card front">
    <svg class="card__edge" viewBox="0 0 540 324" preserveAspectRatio="none" aria-hidden="true">
      <polygon points="0,0 26,0 26,190 70,324 0,324" fill="var(--black)"/>
      <polygon points="26,190 56,190 104,324 70,324" fill="var(--grey)"/>
    </svg>

    <div class="contact-block">
      <h1 class="names">Owen Walsh &amp; Lucy Brand</h1>
      <p class="role">Sales Agents &amp; Onsite Manager</p>
      <address class="address">3/42 Marlow Crescent,<br>FERNLEA QLD 4213</address>
    </div>

    <ul class="phones">
      <li>
        <svg viewBox="0 0 24 24" aria-label="Phone"><path d="M6.6 10.8a15 15 0 0 0 6.6 6.6l2.2-2.2c.3-.3.7-.4 1-.2 1.1.4 2.3.6 3.6.6.6 0 1 .4 1 1V20c0 .6-.4 1-1 1A17 17 0 0 1 3 4c0-.6.4-1 1-1h3.5c.6 0 1 .4 1 1 0 1.3.2 2.5.6 3.6.1.3 0 .7-.2 1z"/></svg>
        07 5948 2063
      </li>
      <li>
        <svg viewBox="0 0 24 24" aria-label="Fax"><path d="M6 2h10v6H6zM3 9h18v9h-3v4H6v-4H3zm5 7v4h8v-4z"/></svg>
        07 5948 2174
      </li>
      <li>
        <svg viewBox="0 0 24 24" aria-label="Mobile"><path d="M7 1h10a2 2 0 0 1 2 2v18a2 2 0 0 1-2 2H7a2 2 0 0 1-2-2V3a2 2 0 0 1 2-2zm0 3v15h10V4zm5 16.2a1 1 0 1 0 0 .1z"/></svg>
        0431 857 219
      </li>
    </ul>

    <div class="brand"><span class="brand__mark"></span>WALSH &amp; BRAND PTY LTD.</div>
  </section>

  <section class="card card--back" aria-label="Card back">
    <svg class="card__edge" viewBox="0 0 540 324" preserveAspectRatio="none" aria-hidden="true">
      <polygon points="540,0 470,0 514,134 514,324 540,324" fill="var(--white)"/>
      <polygon points="436,0 470,0 514,134 484,134" fill="var(--grey)"/>
    </svg>
    <div class="brand"><span class="brand__mark"></span>WALSH &amp; BRAND PTY LTD.</div>
  </section>

</body>
</html>
```